Poloshirt Packaging

We need a very attractive packaging design for our poloshirts. We are wholesaler of the schoolwear market. See what we currently have. I dont want any specific sizing put on the packaging. One design for all poloshirts (2 sides).
our logo is attached aswell

Target Market(s)

Parents

Requirements
Must have
• Our logo
Should not have
• size or age

```html
<!DOCTYPE html>
<html lang="en">
<head>
<meta charset="utf-8">
<title>Brightford Poloshirt Packaging</title>
<link href="https://fonts.googleapis.com/css2?family=Montserrat:wght@600&family=Oswald:wght@300;500;700&display=swap" rel="stylesheet">
<style>
  :root {
    --navy: #173a64;
    --red: #e3242f;
    --white: #ffffff;
    --frame: #222222;
  }
  html, body {
    margin: 0;
    padding: 0;
    overflow: hidden;
    background: var(--white);
  }
  .pack {
    position: relative;
    width: 849px;
    height: 1200px;
    box-sizing: border-box;
    border: 1px solid var(--frame);
    background: var(--white);
    overflow: hidden;
  }
  .brand-name {
    position: absolute;
    left: 0;
    right: 0;
    top: 420px;
    margin: 0;
    text-align: center;
    font-family: "Montserrat", sans-serif;
    font-weight: 600;
    font-size: 124px;
    line-height: 1;
    letter-spacing: -2px;
    color: var(--navy);
  }
  .features {
    position: absolute;
    left: 105px;
    top: 645px;
    width: 636px;
    height: 32px;
    background: var(--navy);
    color: var(--white);
    font-family: "Montserrat", sans-serif;
    font-weight: 600;
    font-size: 18.5px;
    line-height: 32px;
    text-align: center;
    white-space: nowrap;
  }
  .features .divider {
    margin: 0 6px;
    font-weight: 300;
  }
  .band {
    position: absolute;
    left: 0;
    right: 0;
    top: 685px;
    height: 423px;
    background: var(--red);
    color: var(--white);
    text-align: center;
  }
  .product-title {
    margin: 0;
    padding-top: 28px;
    font-family: "Oswald", sans-serif;
    font-weight: 700;
    font-size: 128px;
    line-height: 1;
    letter-spacing: -1px;
  }
  .facts {
    position: absolute;
    left: 0;
    right: 0;
    top: 278px;
    font-family: "Oswald", sans-serif;
    font-weight: 300;
    font-size: 17px;
    line-height: 24.4px;
  }
  .facts h2 {
    margin: 0;
    font-size: 17px;
    font-weight: 500;
  }
  .facts p {
    margin: 0;
  }
</style>
</head>
<body>
  <div class="pack">
    <h1 class="brand-name">Brightford</h1>

    <div class="features">
      Superior weight fabric<span class="divider">|</span>Easy Care - Low iron<span class="divider">|</span>Reactive Dyes
    </div>

    <section class="band">
      <h2 class="product-title">POLOSHIRT</h2>
      <div class="facts">
        <h2>Did you know</h2>
        <p>This Poloshirt Is Sold In 12 Colours</p>
        <p>Reactive Dyed For Superb Colour Fastness</p>
        <p>A Superior Weight Of 210gms</p>
        <p>Strengthened With Twin Needle Stitching</p>
      </div>
    </section>
  </div>
</body>
</html>
```